Redesign of business card for Cedar Ridge Mechanical

We are looking for a new design for our business cards for Cedar Ridge Mechanical. We are a plumbing & HVAC construction company, operating on the West Coast of Canada and USA. Logo attached.
Industry/Entity Type
Construction - Plumbing & HVAC
Contact Information for Business Card
Name, address, phone numbers, email, website address
Look and feel
Each slider illustrates characteristics of the customer's brand and the style your logo design should communicate.

```html
<!DOCTYPE html>
<html lang="en">
<head>
<meta charset="utf-8">
<title>Cedar Ridge Mechanical – Business Card</title>
<link href="https://fonts.googleapis.com/css2?family=Montserrat:wght@400;500;700&display=swap" rel="stylesheet">
<style>
  :root {
    --page-bg: #d8d3cb;
    --card-light: #efe9df;
    --card-mid: #e3dbcf;
    --ink: #1b1a19;
    --ink-soft: #2b2926;
    --band-top: #2a2825;
    --band-bottom: #111111;
    --tan: #cdb99a;
  }
  * { box-sizing: border-box; margin: 0; padding: 0; }
  html, body {
    width: 1200px; height: 1047px; overflow: hidden;
    background: var(--page-bg);
    font-family: "Montserrat", sans-serif;
  }
  .card {
    position: absolute;
    left: 80px; top: 228px;
    width: 1040px; height: 590px;
    border-radius: 24px;
    overflow: hidden;
    background: linear-gradient(135deg, var(--card-light), var(--card-mid));
    box-shadow: 0 10px 30px rgba(0,0,0,0.15);
  }
  .card__band {
    position: absolute;
    left: 0; right: 0; top: 230px; bottom: 0;
    background: linear-gradient(180deg, var(--band-top), var(--band-bottom));
  }
  .holder { position: absolute; left: 14px; top: 50px; }
  .holder__bar {
    position: absolute; left: 0; top: 0;
    width: 18px; height: 72px; background: var(--ink);
  }
  .holder__name {
    position: absolute; left: 30px; top: 0; white-space: nowrap;
    font-weight: 700; font-size: 39px; letter-spacing: 0.5px; color: var(--ink);
    line-height: 1.1;
  }
  .holder__title {
    position: absolute; left: 30px; top: 48px; white-space: nowrap;
    font-weight: 500; font-size: 26px; color: var(--ink-soft);
  }
  .brand {
    position: absolute; right: 40px; top: 78px;
    display: flex; align-items: center; gap: 22px;
  }
  .brand__square { width: 70px; height: 70px; background: var(--ink); }
  .brand__name {
    font-weight: 700; font-size: 40px; line-height: 1.15;
    color: var(--ink); letter-spacing: 1px;
  }
  .contact {
    position: absolute; left: 42px; top: 284px;
    color: var(--tan); font-size: 27px; font-weight: 400;
  }
  .contact__address { line-height: 38px; margin-bottom: 22px; }
  .contact__list { list-style: none; }
  .contact__item { display: flex; align-items: center; gap: 10px; height: 38.5px; }
  .contact__icon { width: 22px; height: 22px; flex: none; }
</style>
</head>
<body>
  <section class="card">
    <div class="card__band" role="img" aria-label="Dark decorative band across the lower card"></div>

    <div class="holder">
      <span class="holder__bar"></span>
      <h1 class="holder__name">DANIEL HAYES</h1>
      <p class="holder__title">Managing Director</p>
    </div>

    <div class="brand">
      <span class="brand__square"></span>
      <p class="brand__name">CEDAR RIDGE<br>MECHANICAL</p>
    </div>

    <div class="contact">
      <p class="contact__address">Your address, City<br>State, Zip 1234</p>
      <ul class="contact__list">
        <li class="contact__item">
          <svg class="contact__icon" viewBox="0 0 24 24"><path d="M6.6 10.8a15 15 0 0 0 6.6 6.6l2.2-2.2c.3-.3.7-.4 1-.2 1.1.4 2.3.6 3.6.6.6 0 1 .4 1 1V20c0 .6-.4 1-1 1A17 17 0 0 1 3 4c0-.6.4-1 1-1h3.5c.6 0 1 .4 1 1 0 1.3.2 2.5.6 3.6.1.3 0 .7-.2 1z" fill="var(--tan)"/></svg>
          123 456 789
        </li>
        <li class="contact__item">
          <svg class="contact__icon" viewBox="0 0 24 24"><rect x="6" y="2" width="12" height="20" rx="2" fill="none" stroke="var(--tan)" stroke-width="2"/><circle cx="12" cy="18" r="1.2" fill="var(--tan)"/></svg>
          123 456 789
        </li>
        <li class="contact__item">
          <svg class="contact__icon" viewBox="0 0 24 24"><rect x="2" y="5" width="20" height="14" rx="1.5" fill="none" stroke="var(--tan)" stroke-width="2"/><path d="M3 6l9 7 9-7" fill="none" stroke="var(--tan)" stroke-width="2"/></svg>
          info@yourmail.com
        </li>
        <li class="contact__item">
          <svg class="contact__icon" viewBox="0 0 24 24"><circle cx="12" cy="12" r="9" fill="none" stroke="var(--tan)" stroke-width="2"/><path d="M3 12h18M12 3c3 3 3 15 0 18M12 3c-3 3-3 15 0 18" fill="none" stroke="var(--tan)" stroke-width="1.5"/></svg>
          www.yourwebsite.com
        </li>
      </ul>
    </div>
  </section>
</body>
</html>
```